Mobile welding fabrication and repair, heavy equipment and semi repair

We need a business card design that will catch the eye but look prelesional at the same time. Were based out of Idaho and we do all welding fabrication jobs and repairs, we also build and install custom pipe fences for personal or larger scale fence jobs and can give free quotes. We can do semi truck and trailer repairs Mobily also.

Target Market(s)

Welding

Industry/Entity Type

welding and repair

Contact Information for Business Card

email (ravenforgeandmend@mailbay.net, phone number 208-417-3826, owner (Dalton Whitcomb), Pipe Fence, Semi Repair, Mobile welding and fabrication

Font styles to use
Sans Serif

Requirements
Must have
• My logo in black background on one side , and other side my logo in white back round with all the information listed on card details
Nice to have
• make it stand out from other business cards

```html
<!DOCTYPE html>
<html lang="en">
<head>
<meta charset="utf-8">
<title>Ravenforge and Mend – Business Card</title>
<link href="https://fonts.googleapis.com/css2?family=Lato:ital,wght@0,400;0,700;0,900;1,400;1,700&display=swap" rel="stylesheet">
<style>
  :root {
    --backdrop: #2a2a2a;
    --card-white: #ffffff;
    --card-black: #111111;
    --brand-blue: #0a63c4;
    --brand-blue-deep: #0649a8;
    --brand-blue-light: #0f9ed8;
    --ink: #1a1a1a;
    --faint-mark: #050505;
  }
  * { margin: 0; padding: 0; box-sizing: border-box; }
  html, body { width: 1075px; height: 1200px; overflow: hidden; background: var(--backdrop); }
  body { position: relative; font-family: "Lato", sans-serif; }

  .card {
    position: absolute;
    width: 659px;
    height: 395px;
    border-radius: 27px;
    overflow: hidden;
    box-shadow: 3px 3px 0 #000, 4px 6px 10px rgba(0,0,0,.45);
  }
  .card--front { left: 208px; top: 187px; background: var(--card-white); }
  .card--back  { left: 210px; top: 638px; width: 657px; background: var(--card-black); }

  .brand-square {
    position: absolute;
    width: 360px;
    height: 360px;
    border-radius: 80px;
  }
  .card--front .brand-square {
    left: 357px; top: 72px;
    background: linear-gradient(180deg, var(--brand-blue-deep), var(--brand-blue-light));
  }
  .card--back .brand-square {
    left: 397px; top: 91px;
    background: var(--faint-mark);
  }

  .owner-name {
    position: absolute; left: 27px; top: 40px;
    font-size: 25px; font-weight: 700; font-style: italic;
    color: var(--brand-blue); letter-spacing: -0.3px;
  }
  .owner-title {
    position: absolute; left: 27px; top: 70px;
    font-size: 19px; font-style: italic; color: var(--ink); letter-spacing: .5px;
  }
  .contact {
    position: absolute; left: 27px; display: flex; align-items: center; gap: 6px;
    font-size: 18px; color: var(--ink);
  }
  .contact--phone { top: 113px; }
  .contact--email { top: 137px; font-style: italic; }
  .contact svg { width: 18px; height: 16px; fill: var(--brand-blue); }

  .services { position: absolute; left: 34px; top: 224px; list-style: none; }
  .services li {
    display: flex; align-items: center; gap: 12px;
    font-size: 17.5px; color: var(--ink); height: 29.5px;
  }
  .services li::before {
    content: ""; width: 9px; height: 9px; border-radius: 50%;
    background: var(--brand-blue);
  }

  .company-name {
    position: absolute; left: 0; right: 0; top: 150px;
    text-align: center;
    font-weight: 900; font-size: 46px; line-height: 1;
    color: var(--brand-blue); letter-spacing: 1px; text-transform: uppercase;
  }
</style>
</head>
<body>

<section class="card card--front" aria-label="Business card front">
  <div class="brand-square" aria-hidden="true"></div>
  <h1 class="owner-name">DALTON WHITCOMB</h1>
  <p class="owner-title">OWNER</p>
  <p class="contact contact--phone">
    <svg viewBox="0 0 24 24" aria-hidden="true"><path d="M6.6 10.8a15.1 15.1 0 0 0 6.6 6.6l2.2-2.2c.3-.3.7-.4 1-.2 1.1.4 2.3.6 3.6.6.6 0 1 .4 1 1V20c0 .6-.4 1-1 1A17 17 0 0 1 3 4c0-.6.4-1 1-1h3.5c.6 0 1 .4 1 1 0 1.3.2 2.5.6 3.6.1.3 0 .7-.2 1z"/></svg>
    208-417-3826
  </p>
  <p class="contact contact--email">
    <svg viewBox="0 0 24 18" aria-hidden="true"><path d="M0 0h24v18H0zM2 2v.5l10 7 10-7V2zM2 5v11h20V5l-10 7z"/></svg>
    ravenforgeandmend@mailbay.net
  </p>
  <ul class="services">
    <li>FABRICATION</li>
    <li>MOBILE WELDING</li>
    <li>SEMI REPAIR</li>
    <li>PIPE FENCE</li>
  </ul>
</section>

<section class="card card--back" aria-label="Business card back">
  <div class="brand-square" aria-hidden="true"></div>
  <p class="company-name">Ravenforge<br>and Mend</p>
</section>

</body>
</html>
```